Call Center In Need of Website Design

We are a call center that provides inbound and outbound calling & marketing services for eCommerce store. We would like to see a fun, creative, playful design that is simple.

Here are some sample design sites we like;
- https://www.velmoreline.com/
- https://pindrask.io/
- https://www.glimbertic.com/live-chat-software/
- https://www.zavrolin.com/

Here are some competitor sites;
- https://www.ostrevaglinks.com/
- https://www.helpkestrel.com/

I have attached website content for your use.

Target Market(s)

eCommerce

Coding

Coded - Design and coding required

Number of Pages Required

5+ page

Font styles to use
Sans Serif

Colors

Designer to choose colors to be used in the design.

Requirements
Must have
• Must have designs for the following 5 separate pages;
• 1. Home (landing)
• - This will be were the design style really needs to show.
• - Just needs to touch on key services
• - CTA
• 2. About Us
• - Basic page for about me paragraph
• 3. Services
• - List of services with icons
• - Click on service type to expand details or hover over service icon to view popup bubble with details about that service
• 4. Pricing
• - Option to bundle 1(one) digital service plan and 1(one) call center service plan
• - Bundling adds 10% monthly discount to over all price
• - Customer does NOT have to bundle
• - FAQ
• 5. Contact Us
• - Include a capture form (name, company name, email, phone, message)
• - Contact info
• - Business hours
• When customer purchases their desired plan, then they are taken to a page where they must schedule a call with an account rep.
Nice to have
• home page animations
Should not have
• All information on Home/Landing page.

```html
<!DOCTYPE html>
<html lang="en">
<head>
<meta charset="utf-8">
<title>Orbitly – Customer Care for eCommerce</title>
<link href="https://fonts.googleapis.com/css2?family=Montserrat:wght@400;500;600;700&family=Open+Sans:wght@400;600&display=swap" rel="stylesheet">
<style>
:root{
  --ink:#1b1b1b;
  --text:#333;
  --muted:#9a9a9a;
  --teal:#45bfa3;
  --mint:#b9f6e9;
  --accent-dot:#f07a2a;
  --dark:#151515;
  --footer:#2a2a2a;
  --footer-text:#8a8a8a;
  --line:#cfcfcf;
  --white:#fff;
}
*{margin:0;padding:0;box-sizing:border-box}
html,body{width:1200px;height:2476px;overflow:hidden;background:var(--white)}
body{position:relative;font-family:"Open Sans",Arial,sans-serif;color:var(--text)}
.abs{position:absolute}
.heading{font-family:"Montserrat",Arial,sans-serif;font-weight:500;color:var(--ink)}
.section-title{position:absolute;left:0;width:1200px;text-align:center;font-family:"Montserrat",Arial,sans-serif;font-weight:500;font-size:29px;letter-spacing:5px;color:var(--ink)}

/* header */
.brand{position:absolute;left:160px;top:22px;display:flex;align-items:center;gap:16px}
.brand-mark{width:38px;height:38px;border-radius:50%;border:3px solid var(--teal)}
.brand-name{font-family:"Montserrat",Arial,sans-serif;font-size:27px;font-weight:400;letter-spacing:5px;color:var(--ink)}
.nav{position:absolute;top:30px;left:440px;display:flex;align-items:center;font-family:"Montserrat",Arial,sans-serif;font-size:11.5px;color:var(--text)}
.nav a{color:inherit;text-decoration:none}
.nav .active{color:var(--ink);font-weight:600}
.nav .dot{width:4px;height:4px;border-radius:50%;background:var(--accent-dot);margin:0 15px}
.auth{position:absolute;left:828px;top:30px;font-family:"Montserrat",Arial,sans-serif;font-size:11.5px;color:var(--text)}
.account-btn{position:absolute;left:926px;top:21px;width:111px;height:36px;border:2px solid var(--ink);font-family:"Montserrat",Arial,sans-serif;font-weight:700;font-size:10.5px;letter-spacing:.5px;display:flex;align-items:center;justify-content:center;color:var(--ink)}

/* hero */
.hero-title{left:160px;top:188px;font-size:48px;line-height:56px;font-weight:400}
.hero-text{left:160px;top:322px;font-size:12.5px;line-height:21px;color:var(--muted)}
.btn-mint{display:flex;align-items:center;justify-content:center;gap:6px;background:var(--mint);font-family:"Montserrat",Arial,sans-serif;font-weight:600;font-size:10.5px;color:var(--ink)}
.hero-cta{left:160px;top:404px;width:126px;height:45px}
.divider{top:540px;height:1px;background:var(--line)}
.divider-label{left:290px;top:531px;font-family:"Montserrat",Arial,sans-serif;font-size:12.5px;letter-spacing:2px;color:#777}

/* what we do */
.about-text{left:205px;top:707px;width:790px;text-align:center;font-size:11.5px;line-height:22px;color:#555}

/* services */
.services-card{left:315px;top:955px;width:550px;height:406px;background:var(--white);box-shadow:0 6px 30px rgba(0,0,0,.16)}
.service{position:absolute;left:18px;display:flex}
.service-icon{width:187px;height:134px;border:2px solid var(--teal);box-shadow:3px 4px 8px rgba(0,0,0,.18);display:flex;align-items:center;justify-content:center;background:var(--white)}
.service-body{margin-left:20px;padding-top:14px}
.service-title{font-family:"Montserrat",Arial,sans-serif;font-weight:600;font-size:15.5px;color:var(--ink);margin-bottom:8px}
.service-text{font-size:11.5px;line-height:19px;color:var(--muted);width:300px}
.service-more{width:121px;height:36px;margin-top:14px}
.card-corner{position:absolute;right:0;bottom:0;width:28px;height:28px;background:var(--teal);display:flex;align-items:center;justify-content:center}

/* faq */
.faq-band{left:0;top:1459px;width:1200px;height:392px;background:radial-gradient(ellipse at 50% 40%,#2c2c2c 0%,#121212 75%)}
.faq-band .section-title{color:var(--white);top:76px;letter-spacing:6px}
.faq-item{position:absolute;width:200px;text-align:center}
.faq-icon{position:relative;width:80px;height:80px;margin:0 auto 12px;border:1.5px solid #bbb;border-radius:50%;display:flex;align-items:center;justify-content:center}
.faq-num{position:absolute;left:10px;top:-6px;width:20px;height:20px;border-radius:50%;background:var(--teal);color:var(--white);font-family:"Montserrat",Arial,sans-serif;font-size:11px;font-weight:600;display:flex;align-items:center;justify-content:center}
.faq-q{font-family:"Montserrat",Arial,sans-serif;font-weight:600;font-size:12.5px;line-height:21px;color:var(--white)}

/* testimonials */
.testimonial-name{left:521px;top:2015px;font-family:"Montserrat",Arial,sans-serif;font-weight:600;font-size:16px;color:var(--ink)}
.testimonial-date{left:521px;top:2038px;font-size:11.5px;font-style:italic;color:#555}
.testimonial-rule{left:521px;top:2062px;width:45px;height:2px;background:#999}
.testimonial-text{left:521px;top:2072px;width:300px;font-size:11.5px;line-height:20px;color:#444}
.testimonial-more{left:521px;top:2118px;font-family:"Montserrat",Arial,sans-serif;font-weight:600;font-size:11px;color:var(--ink)}

/* footer */
.footer{left:0;top:2237px;width:1200px;height:239px;background:var(--footer)}
.footer-head{position:absolute;top:78px;font-family:"Montserrat",Arial,sans-serif;font-weight:600;font-size:11.5px;letter-spacing:.5px;color:#bdbdbd}
.contact-row{position:absolute;left:160px;display:flex;align-items:flex-start;gap:14px;font-size:11.5px;line-height:18px;color:var(--footer-text)}
.contact-row svg{flex:none;margin-top:1px}
.links{position:absolute;top:115px;font-size:11.5px;line-height:22.5px;color:var(--footer-text);list-style:none}
.social{position:absolute;left:827px;top:58px;display:flex;gap:16px}
.social span{width:40px;height:40px;border:1.5px solid #d8d8d8}
.copyright{position:absolute;right:162px;top:114px;text-align:right;font-size:11px;line-height:19px;color:var(--footer-text)}
</style>
</head>
<body>

<!-- Header -->
<div class="brand"><span class="brand-mark"></span><span class="brand-name">ORBITLY</span></div>
<nav class="nav">
  <a class="active">Home</a><span class="dot"></span>
  <a>About Us</a><span class="dot"></span>
  <a>Services</a><span class="dot"></span>
  <a>Pricing</a><span class="dot"></span>
  <a>Contact Us</a>
</nav>
<div class="auth">Login&nbsp; | &nbsp;Register</div>
<div class="account-btn">ACCOUNT</div>

<!-- Hero -->
<svg class="abs" style="left:0;top:0" width="1200" height="600" role="img" aria-label="Photo of a smiling customer support agent wearing a headset in an office">
  <defs>
    <linearGradient id="heroPhoto" x1="0" y1="0" x2="1" y2="1">
      <stop offset="0" stop-color="#b9c3cc"/>
      <stop offset=".5" stop-color="#8c98a6"/>
      <stop offset="1" stop-color="#5d6470"/>
    </linearGradient>
  </defs>
  <path d="M1140 50 L1200 50 L1200 520 Q1110 586 960 586 Q790 586 718 470 Q690 385 765 305 Z" fill="url(#heroPhoto)"/>
</svg>
<h1 class="abs heading hero-title">Orbitly is built to support<br>small business</h1>
<p class="abs hero-text">Orbitly is an omnichannel provider for customer care and back-end office support.<br>We primarily work with eCommerce companies around the world.</p>
<div class="abs btn-mint hero-cta">Contact Us <span>&rarr;</span></div>
<div class="abs divider" style="left:0;width:280px"></div>
<div class="abs divider-label">ORBITLY</div>
<div class="abs divider" style="left:360px;width:350px"></div>

<!-- What we do -->
<h2 class="section-title" style="top:657px">WHAT WE DO</h2>
<p class="abs about-text">Orbitly is your personal customer service and product research team. We love eCommerce, but we love seeing business owners succeed even more! That is exactly why we have developed the processes and technology to take care of the most over looked areas in eCommerce Customer Service and Retention. Let Orbitly handle your customers while you focus on growing your business.</p>

<!-- Services -->
<svg class="abs" style="left:0;top:690px" width="420" height="600" role="img" aria-label="Photo of a smiling call center agent with a headset">
  <defs>
    <linearGradient id="servicePhoto" x1="0" y1="0" x2="1" y2="1">
      <stop offset="0" stop-color="#3a3f55"/>
      <stop offset=".45" stop-color="#c9a891"/>
      <stop offset="1" stop-color="#eceae8"/>
    </linearGradient>
  </defs>
  <path d="M0 3 L400 270 L325 550 Q305 597 250 597 Q205 597 165 572 L0 498 Z" fill="url(#servicePhoto)"/>
</svg>
<h2 class="section-title" style="top:876px">OUR SERVICES</h2>
<div class="abs services-card">
  <div class="service" style="top:50px">
    <div class="service-icon">
      <svg width="90" height="80" viewBox="0 0 90 80" fill="none">
        <rect x="5" y="18" width="72" height="46" rx="3" fill="var(--teal)"/>
        <rect x="11" y="24" width="60" height="34" fill="#fff"/>
        <rect x="34" y="64" width="14" height="8" fill="var(--teal)"/>
        <rect x="24" y="72" width="34" height="4" rx="2" fill="var(--teal)"/>
        <circle cx="32" cy="42" r="9" stroke="var(--teal)" stroke-width="4" stroke-dasharray="4 2.6"/>
        <circle cx="52" cy="48" r="6" stroke="var(--teal)" stroke-width="3.5" stroke-dasharray="3 2.2"/>
        <circle cx="70" cy="16" r="12" fill="var(--teal)"/>
        <circle cx="70" cy="16" r="4.5" fill="#fff"/>
      </svg>
    </div>
    <div class="service-body">
      <div class="service-title">Digital Services</div>
      <div class="service-text">Orbitly is an omnichannel provider for customer care and back-end office support.</div>
      <div class="btn-mint service-more">Learn More <span>&rarr;</span></div>
    </div>
  </div>
  <div class="service" style="top:216px">
    <div class="service-icon">
      <svg width="80" height="90" viewBox="0 0 80 90" fill="none">
        <circle cx="40" cy="34" r="17" fill="var(--teal)"/>
        <path d="M18 34 A22 22 0 0 1 62 34" stroke="var(--teal)" stroke-width="4"/>
        <rect x="13" y="30" width="8" height="14" rx="3" fill="var(--teal)"/>
        <rect x="59" y="30" width="8" height="14" rx="3" fill="var(--teal)"/>
        <path d="M20 44 Q22 56 36 56" stroke="var(--teal)" stroke-width="3"/>
        <path d="M6 88 Q8 62 40 60 Q72 62 74 88 Z" fill="var(--teal)"/>
      </svg>
    </div>
    <div class="service-body">
      <div class="service-title">Call Center Services</div>
      <div class="service-text">Orbitly is an omnichannel provider for customer care and back-end office support.</div>
      <div class="btn-mint service-more">Learn More <span>&rarr;</span></div>
    </div>
  </div>
  <div class="card-corner">
    <svg width="14" height="12" viewBox="0 0 14 12" fill="none" stroke="#fff" stroke-width="2"><path d="M2 1l5 5-5 5M7 1l5 5-5 5"/></svg>
  </div>
</div>

<!-- FAQ -->
<section class="abs faq-band">
  <h2 class="section-title">FREQUENTLY ASKED QUESTIONS</h2>
  <div class="faq-item" style="left:152px;top:143px">
    <div class="faq-icon"><span class="faq-num">1</span>
      <svg width="40" height="34" viewBox="0 0 40 34" fill="none"><path d="M3 3h22v15H13l-6 5v-5H3z" fill="#fff"/><path d="M14 11h23v16h-4v5l-6-5H14z" fill="#fff" stroke="#151515" stroke-width="2"/><text x="25.5" y="24" font-family="Montserrat,Arial,sans-serif" font-size="12" font-weight="700" fill="#151515" text-anchor="middle">?</text></svg>
    </div>
    <div class="faq-q">Do I have to purchase any<br>hardware or equipment?</div>
  </div>
  <div class="faq-item" style="left:382px;top:196px">
    <div class="faq-icon"><span class="faq-num">2</span>
      <svg width="40" height="34" viewBox="0 0 40 34" fill="none"><path d="M3 3h22v15H13l-6 5v-5H3z" fill="#fff"/><path d="M14 11h23v16h-4v5l-6-5H14z" fill="#fff" stroke="#151515" stroke-width="2"/><text x="25.5" y="24" font-family="Montserrat,Arial,sans-serif" font-size="12" font-weight="700" fill="#151515" text-anchor="middle">?</text></svg>
    </div>
    <div class="faq-q">Do I have to purchase any<br>hardware or equipment?</div>
  </div>
  <div class="faq-item" style="left:634px;top:196px">
    <div class="faq-icon"><span class="faq-num">3</span>
      <svg width="40" height="34" viewBox="0 0 40 34" fill="none"><path d="M3 3h22v15H13l-6 5v-5H3z" fill="#fff"/><path d="M14 11h23v16h-4v5l-6-5H14z" fill="#fff" stroke="#151515" stroke-width="2"/><text x="25.5" y="24" font-family="Montserrat,Arial,sans-serif" font-size="12" font-weight="700" fill="#151515" text-anchor="middle">?</text></svg>
    </div>
    <div class="faq-q">I'm not sure how many<br>minutes I'll need?</div>
  </div>
  <div class="faq-item" style="left:869px;top:143px">
    <div class="faq-icon"><span class="faq-num">4</span>
      <svg width="40" height="34" viewBox="0 0 40 34" fill="none"><path d="M3 3h22v15H13l-6 5v-5H3z" fill="#fff"/><path d="M14 11h23v16h-4v5l-6-5H14z" fill="#fff" stroke="#151515" stroke-width="2"/><text x="25.5" y="24" font-family="Montserrat,Arial,sans-serif" font-size="12" font-weight="700" fill="#151515" text-anchor="middle">?</text></svg>
    </div>
    <div class="faq-q">How long does it take<br>to get started?</div>
  </div>
</section>

<!-- Testimonials -->
<h2 class="section-title" style="top:1924px">OUR TESTIMONIALS</h2>
<svg class="abs" style="left:320px;top:1985px" width="560" height="185">
  <defs>
    <filter id="cardShadow" x="-10%" y="-20%" width="120%" height="140%"><feDropShadow dx="0" dy="3" stdDeviation="5" flood-opacity=".18"/></filter>
    <linearGradient id="clientPhoto" x1="0" y1="0" x2="0" y2="1"><stop offset="0" stop-color="#e9e4df"/><stop offset="1" stop-color="#6f6a69"/></linearGradient>
  </defs>
  <path d="M100 12 H468 L546 90 L468 168 H100 Z" fill="#fff" filter="url(#cardShadow)"/>
  <rect x="55" y="34" width="110" height="110" transform="rotate(45 110 89)" fill="#fff" stroke="#111" stroke-width="7"/>
  <rect x="68" y="47" width="84" height="84" transform="rotate(45 110 89)" fill="url(#clientPhoto)" role="img" aria-label="Portrait photo of the client"/>
  <g fill="#fff" stroke="#333" stroke-width="1.3">
    <rect x="513" y="20" width="24" height="24" transform="rotate(45 525 32)"/>
    <rect x="513" y="132" width="24" height="24" transform="rotate(45 525 144)"/>
  </g>
  <path d="M519 35l6-6 6 6M519 141l6 6 6-6" fill="none" stroke="#333" stroke-width="1.3"/>
</svg>
<div class="abs testimonial-name">Daniel Forsythe</div>
<div class="abs testimonial-date">10 july-2018</div>
<div class="abs testimonial-rule"></div>
<p class="abs testimonial-text">Lorem Ipsum is simply dummy text of the printing and typesetting industry. Lorem Ipsum the industry's</p>
<div class="abs testimonial-more">Learn More &rarr;</div>

<!-- Footer -->
<footer class="abs footer">
  <div class="footer-head" style="left:160px">KEEP IN TOUCH</div>
  <div class="contact-row" style="top:112px">
    <svg width="18" height="16" viewBox="0 0 18 16" fill="#888"><path d="M3 1l3 0 1.5 4-2 1.3a9 9 0 0 0 4.2 4.2L11 8.5 15 10v3c0 1-1 2-2 2A12 12 0 0 1 1 3c0-1 1-2 2-2z"/></svg>
    <span>(800) 555-0148</span>
  </div>
  <div class="contact-row" style="top:140px">
    <svg width="18" height="14" viewBox="0 0 18 14" fill="none" stroke="#888" stroke-width="1.4"><rect x="1" y="1" width="16" height="12"/><path d="M1 1l8 7 8-7"/></svg>
    <span>info@orbitly.com</span>
  </div>
  <div class="contact-row" style="top:170px">
    <svg width="18" height="16" viewBox="0 0 18 16" fill="#888"><path d="M9 1L1 8h2.5v7h4v-4h3v4h4V8H17z"/></svg>
    <span>Orbitly, Inc. 418 Alder Row,<br>Fresno, CA 93710</span>
  </div>

  <div class="footer-head" style="left:488px;top:76px">QUICK LINKS</div>
  <ul class="links" style="left:488px;top:112px"><li>Home</li><li>About Us</li><li>Services</li><li>Pricing</li></ul>
  <ul class="links" style="left:660px;top:112px"><li>Contact Us</li><li>Help</li><li>Support</li></ul>

  <div class="social"><span></span><span></span><span></span><span></span></div>
  <div class="copyright">Copyright &copy; 2018 Orbitly<br>All Rights Reserved</div>
</footer>

</body>
</html>
```